Brindle Haven Website design in word press

Develop great looking website home page with basic menus in Word Press. We already have a logo, so no need to re-invent that.

Target Market(s)

donors, animal owners, emergency services.

Number of Pages Required

1 page

Font styles to use
Sans Serif

Colors
ec1f27
000000
ffffff
959595

Requirements
Must have
• Fresh design in Word Press, neutral (i.e. not American looking), uses red, black and white as core colours. Needs to have menu options for about us, join us, help us, FAQs, contact us etc. Looking for a smart, modern, professional looking home page, that we can easily add pages/menu's/widgets to. Include social media buttons for facebook, twitter etc.
Nice to have
• Images (could be in colour shades) of animals in disaster i.e. search royalty free Hurricane Lorimel, Hurrican Odwin.
Should not have
• Images that breach copyright.

```html
<!DOCTYPE html>
<html lang="en">
<head>
<meta charset="utf-8">
<title>Brindle Haven New Zealand Trust</title>
<link rel="stylesheet" href="https://fonts.googleapis.com/css2?family=Montserrat:wght@400;500;600&family=Arimo:wght@400;700&display=swap">
<style>
:root{
  --red:#ec1f27;
  --red-deep:#e2001f;
  --black:#000000;
  --ink:#222222;
  --body:#444444;
  --grey:#959595;
  --line:#d8d8d8;
  --white:#ffffff;
  --footer:#1c1c1c;
}
*{box-sizing:border-box;margin:0;padding:0}
html,body{width:1200px;height:2456px;overflow:hidden;background:var(--white)}
body{position:relative;font-family:"Arimo",Arial,sans-serif;color:var(--body)}
.abs{position:absolute}
h1,h2,h3,.nav a,.btn,.card-bar{font-family:"Montserrat",Arial,sans-serif}

/* header */
.site-header{left:0;top:0;width:1200px;height:108px;border-top:3px solid var(--red);background:var(--white)}
.brand{left:86px;top:20px;display:flex;align-items:center;gap:12px}
.brand-dot{width:66px;height:66px;border-radius:50%;background:var(--red)}
.brand-name{font-family:"Montserrat",Arial,sans-serif;font-weight:600;font-size:15px;color:var(--red);line-height:1.25}
.search{left:887px;top:18px;width:226px;height:38px;border:1px solid #cfcfcf;font-size:12px;color:#333;padding:11px 12px;font-family:"Montserrat",Arial,sans-serif}
.search svg{position:absolute;right:12px;top:12px}
.nav{left:0;top:76px;width:1200px;height:20px}
.nav a{position:absolute;font-size:12.5px;font-weight:500;color:#222;text-decoration:none;letter-spacing:.2px}
.nav a.active{color:var(--red)}

/* hero */
.hero{left:0;top:108px;width:1200px;height:549px;background:linear-gradient(180deg,#4d5b4a 0%,#6d7a62 30%,#8a8677 55%,#7a6d64 80%,#5e5550 100%)}
.hero-panel{left:571px;top:403px;width:495px;height:224px;background:rgba(40,40,40,.78);padding:22px 34px}
.hero-panel h1{font-size:48px;font-weight:400;color:var(--red);line-height:1;letter-spacing:1px}
.hero-panel h2{font-size:25px;font-weight:400;color:var(--white);margin-top:6px;letter-spacing:.5px}
.hero-panel p{font-size:12px;line-height:26px;color:#eee;margin-top:14px}

/* cards */
.card{top:696px;width:323px;height:226px}
.card-photo{width:100%;height:183px}
.card-bar{height:44px;display:flex;align-items:center;justify-content:space-between;padding:0 16px;color:var(--white);font-size:18px;letter-spacing:.5px;background:rgba(50,50,50,.9)}
.card-bar.red{background:var(--red)}
.card-shadow{position:absolute;left:8px;right:8px;bottom:-10px;height:10px;background:radial-gradient(ellipse at top,rgba(0,0,0,.25),transparent 70%)}

/* welcome */
.section-title{font-size:23px;font-weight:400;color:var(--ink);letter-spacing:.3px}
.section-title span{color:var(--red)}
.welcome{left:87px;top:1005px;width:603px}
.welcome p{font-size:11.5px;line-height:22px;color:#333;margin-top:22px}
.welcome p + p{margin-top:22px}
.btn{display:inline-block;font-size:12.5px;color:var(--white);background:var(--red-deep);padding:13px 16px;border-radius:3px;margin-top:18px;letter-spacing:.3px}
.howto{left:745px;top:1005px;width:370px}
.howto ul{list-style:none;margin-top:22px}
.howto li{position:relative;padding-left:28px;font-size:11.5px;line-height:22px;color:#333;margin-bottom:12px}
.howto li svg{position:absolute;left:2px;top:6px}

/* organisation */
.org-photo{left:0;top:1367px;width:561px;height:381px;background:linear-gradient(160deg,#7a7f80 0%,#5d6062 45%,#3d3a38 100%)}
.org-panel{left:561px;top:1367px;width:639px;height:381px;background:var(--red-deep)}
.org-mark{left:592px;top:1404px;width:175px;height:175px;border-radius:50%;border:8px solid var(--white)}
.org-text{left:785px;top:1405px;width:323px;color:var(--white)}
.org-text h3{font-size:19px;font-weight:500;letter-spacing:.5px}
.org-text p{font-size:11.5px;line-height:24px;margin-top:18px;text-align:justify}
.btn-outline{position:absolute;left:789px;top:1667px;width:129px;height:41px;border:2px solid var(--white);color:var(--white);font-size:12.5px;display:flex;align-items:center;justify-content:center;letter-spacing:.3px}

/* trust */
.trust{left:0;top:1793px;width:1200px;text-align:center}
.trust h2{font-size:21px;font-weight:500;color:var(--red-deep);letter-spacing:.3px}
.trust p.lead{font-size:12px;color:#444;margin-top:22px}
.action{top:1888px;width:300px;text-align:center}
.action-icon{display:block;margin:0 auto}
.action h3{font-size:15px;font-weight:500;color:var(--red-deep);margin-top:16px;letter-spacing:.3px}
.action p{font-size:12px;line-height:25px;color:#444;margin-top:10px}

/* footer */
.site-footer{left:0;top:2153px;width:1200px;height:303px;background:var(--footer)}
.foot-brand{left:480px;top:2185px;display:flex;align-items:center;gap:14px}
.foot-brand .brand-dot{width:90px;height:90px;border:5px solid var(--white);background:transparent}
.foot-brand .brand-name{color:var(--white)}
.foot-rule{left:87px;top:2299px;width:1026px;height:1px;background:#3a3a3a}
.social{top:2321px;width:60px;height:60px;border-radius:50%;border:1px solid #8a8a8a;display:flex;align-items:center;justify-content:center}
.copyright{left:0;top:2411px;width:1200px;text-align:center;color:var(--white);font-size:12px;line-height:16px}
</style>
</head>
<body>

<header class="site-header abs">
  <div class="brand abs">
    <div class="brand-dot"></div>
    <div class="brand-name">BRINDLE HAVEN.NZ<br>TIAKI KARAREHE</div>
  </div>
  <div class="search abs">SEARCH
    <svg width="12" height="12" viewBox="0 0 12 12"><circle cx="5" cy="5" r="3.8" fill="none" stroke="#333" stroke-width="1.6"/><line x1="7.8" y1="7.8" x2="11" y2="11" stroke="#333" stroke-width="1.8"/></svg>
  </div>
  <nav class="nav abs">
    <a class="active" style="left:537px">HOME</a>
    <a style="left:628px">ABOUT US</a>
    <a style="left:743px">JOIN US</a>
    <a style="left:845px">HELP US</a>
    <a style="left:948px">FAQS</a>
    <a style="left:1034px">CONTACT US</a>
  </nav>
</header>

<section class="hero abs" role="img" aria-label="Rescuers wading through a flooded street while a boat ferries people and pets to safety"></section>
<div class="hero-panel abs">
  <h1>BRINDLE</h1>
  <h2>HAVEN NEW ZEALAND TRUST</h2>
  <p>As we receive no government funding, Brindle Haven needs your help so that animals are not left behind in emergencies.Formed in 2018, following the devastat the year prior that saw over 1,000 animals left behind</p>
</div>

<div class="card abs" style="left:87px">
  <div class="card-photo" role="img" aria-label="Evacuees carrying their dogs through heavy rain and floodwater" style="background:linear-gradient(160deg,#8b9091,#5a5c5e 60%,#3b3937)"></div>
  <div class="card-bar red">ABOUT US <svg width="16" height="16" viewBox="0 0 16 16"><circle cx="8" cy="8" r="6.5" fill="none" stroke="#fff" stroke-width="1.6"/><path d="M6.5 5l3 3-3 3" fill="none" stroke="#fff" stroke-width="1.8"/></svg></div>
  <div class="card-shadow"></div>
</div>
<div class="card abs" style="left:439px">
  <div class="card-photo" role="img" aria-label="Volunteers paddling a kayak down a flooded tree-lined road" style="background:linear-gradient(180deg,#5d7048,#7e8466 50%,#8a7d63)"></div>
  <div class="card-bar">WHAT WE DO <svg width="16" height="16" viewBox="0 0 16 16"><circle cx="8" cy="8" r="6.5" fill="none" stroke="#fff" stroke-width="1.6"/><path d="M6.5 5l3 3-3 3" fill="none" stroke="#fff" stroke-width="1.8"/></svg></div>
  <div class="card-shadow"></div>
</div>
<div class="card abs" style="left:790px">
  <div class="card-photo" role="img" aria-label="Rescuers in boats on a flooded street at dusk" style="background:linear-gradient(180deg,#6f8aa6,#8a8e86 50%,#4e5a5e)"></div>
  <div class="card-bar">OUR HOPE <svg width="16" height="16" viewBox="0 0 16 16"><circle cx="8" cy="8" r="6.5" fill="none" stroke="#fff" stroke-width="1.6"/><path d="M6.5 5l3 3-3 3" fill="none" stroke="#fff" stroke-width="1.8"/></svg></div>
  <div class="card-shadow"></div>
</div>

<section class="welcome abs">
  <h2 class="section-title">WELCOME TO <span>BRINDLE HAVEN</span></h2>
  <p>Formed in 2018, following the devastating Harwell Flats flood the year prior that saw over 1,000 animals left behind in need of rescue, Brindle Haven New Zealand (Tiaki Kararehe) is a charity comprised of volunteers including veterinary and disaster response professionals, to ensure the needs of animals are better served in future emergencies. Though there is a primary focus on companion animals,</p>
  <p>Brindle Haven works to advocate for all animals that are vulnerable or affected by disasters. A national pool of trained Brindle Haven volunteers will be established to provide surge capacity in support of regional animal welfare emergency response. Your funding will help us establish such capacity with a goal</p>
  <span class="btn">READ MORE INFO</span>
</section>

<section class="howto abs">
  <h2 class="section-title">HOW <span>WE DO IT</span></h2>
  <ul>
    <li><svg width="12" height="10" viewBox="0 0 12 10"><path d="M1 5l3.5 3.5L11 1.5" fill="none" stroke="#ec1f27" stroke-width="2.4"/></svg>We are the leading voice for all animals affected by disaster</li>
    <li><svg width="12" height="10" viewBox="0 0 12 10"><path d="M1 5l3.5 3.5L11 1.5" fill="none" stroke="#ec1f27" stroke-width="2.4"/></svg>We act to do the right thing for the animals in a disaster management context</li>
    <li><svg width="12" height="10" viewBox="0 0 12 10"><path d="M1 5l3.5 3.5L11 1.5" fill="none" stroke="#ec1f27" stroke-width="2.4"/></svg>We develop local capacity to create animal inclusive community resilience</li>
    <li><svg width="12" height="10" viewBox="0 0 12 10"><path d="M1 5l3.5 3.5L11 1.5" fill="none" stroke="#ec1f27" stroke-width="2.4"/></svg>We hold to account those with responsibilities to protect animals from disaster</li>
    <li><svg width="12" height="10" viewBox="0 0 12 10"><path d="M1 5l3.5 3.5L11 1.5" fill="none" stroke="#ec1f27" stroke-width="2.4"/></svg>We inform our position and activities using best practice and scientific knowledge</li>
  </ul>
</section>

<div class="org-photo abs" role="img" aria-label="A man wading through floodwater carrying two dogs, with other evacuees behind him in the rain"></div>
<div class="org-panel abs"></div>
<div class="org-mark abs"></div>
<div class="org-text abs">
  <h3>ORGANISATION DETAILS</h3>
  <p>Brindle Haven New Zealand is a registered charitable trust under the Charitable Trusts Act 1957. We are the NZ's only dedicated emergency management charity for animals, with a mission to protect animals from disasters.</p>
  <p>A national pool of trained Brindle Haven volunteers will be established to provide surge capacity in support of regional animal welfare emergency response</p>
</div>
<span class="btn-outline">READ MORE</span>

<section class="trust abs">
  <h2>BRINDLE HAVEN NEW ZEALAND TRUST</h2>
  <p class="lead">As we receive no government funding, Brindle Haven needs your help so that animals are not left behind in emergencies.</p>
</section>

<div class="action abs" style="left:103px">
  <svg class="action-icon" width="120" height="120" viewBox="0 0 120 120"><circle cx="60" cy="60" r="56" fill="none" stroke="#e2001f" stroke-width="6"/><circle cx="60" cy="60" r="40" fill="#e2001f"/><path d="M60 76 L45 61 a8.5 8.5 0 0 1 15-10 a8.5 8.5 0 0 1 15 10z" fill="#fff"/></svg>
  <h3>DONATE NOW</h3>
  <p>Brindle Haven New Zealand (Tiaki charity<br>comprised of volunteers</p>
</div>
<div class="action abs" style="left:450px">
  <svg class="action-icon" width="120" height="120" viewBox="0 0 120 120"><circle cx="60" cy="60" r="56" fill="none" stroke="#e2001f" stroke-width="6"/><circle cx="60" cy="60" r="40" fill="#e2001f"/><rect x="47" y="42" width="26" height="34" rx="2" fill="none" stroke="#fff" stroke-width="2.4"/><rect x="54" y="39" width="12" height="6" fill="#fff"/><g stroke="#fff" stroke-width="2"><line x1="52" y1="53" x2="68" y2="53"/><line x1="52" y1="60" x2="68" y2="60"/><line x1="52" y1="67" x2="68" y2="67"/></g></svg>
  <h3>ADD TO PLAN</h3>
  <p>Brindle Haven New Zealand (Tiaki charity<br>comprised of volunteers</p>
</div>
<div class="action abs" style="left:797px">
  <svg class="action-icon" width="120" height="120" viewBox="0 0 120 120"><circle cx="60" cy="60" r="56" fill="none" stroke="#e2001f" stroke-width="6"/><circle cx="60" cy="60" r="40" fill="#e2001f"/><circle cx="62" cy="50" r="9" fill="none" stroke="#fff" stroke-width="2.4"/><path d="M42 66 h14 l8 4 h12 v6 H42z" fill="none" stroke="#fff" stroke-width="2.4" stroke-linejoin="round"/></svg>
  <h3>HELP FUNDRAISE</h3>
  <p>Brindle Haven New Zealand (Tiaki charity<br>comprised of volunteers</p>
</div>

<footer class="site-footer abs"></footer>
<div class="foot-brand abs">
  <div class="brand-dot"></div>
  <div class="brand-name">BRINDLE HAVEN.NZ<br>TIAKI KARAREHE</div>
</div>
<div class="foot-rule abs"></div>
<a class="social abs" style="left:391px" aria-label="Social profile"></a>
<a class="social abs" style="left:463px" aria-label="Social profile"></a>
<a class="social abs" style="left:533px" aria-label="Social profile"></a>
<a class="social abs" style="left:607px" aria-label="Social profile"></a>
<a class="social abs" style="left:676px" aria-label="Social profile"></a>
<a class="social abs" style="left:749px" aria-label="Email"><svg width="18" height="14" viewBox="0 0 18 14"><rect x="1" y="1" width="16" height="12" rx="1.5" fill="none" stroke="#fff" stroke-width="1.5"/><path d="M1.5 2l7.5 6 7.5-6" fill="none" stroke="#fff" stroke-width="1.5"/></svg></a>
<div class="copyright abs">© Copyrights 2018 Brindle Haven.All Rights Reserved.</div>

</body>
</html>
```